Coastal Learner Bureau business cards

Australian company about to start offering its services. We recruit international students to come to study English, vocational education and postgraduate courses in Australia. We help them find the institution and select the right city they want to come to Australia. We are a young, online oriented and supportive agency. Our clients are between 18 and 35 years old, mainly University students, young professionals or people with work experience. We provide much more information that any other agency offer. We administrate a Facebook group with more than 11.000 members that daily ask questions about general information when coming to Australia, while they are here and even after they leave the country

Target Market(s)

International students from South America, Central America and Europe

Industry/Entity Type

Student

Contact Information for Business Card

Tomas Bilbrea
Managing Director
tomas@kelvarin.com.au
www.kelvoria.com.au
+61 491058264
Melbourne, Australia

Font styles to use
Serif
Sans Serif

Colors

Designer to choose colors to be used in the design.

Requirements
Must have
• Horizontal design
• Standard business card size and shape. If font uses green or yellow colours, they will have to match the ones from the logo
Nice to have
• UPDATE: Use the contents of the green image to design one of the card sides. Use our logo in the background of that side as watermark.
• Passport image, or immigration stamps. A picture of the Yarra River (from Melbourne) would be cool as well.
Should not have
• Non-standard business card size and shape
• Not black as the background colour of any sides as we are not a VIP agency or a hight class service. We are orientes to young people and they like colours, pictures, something attractive.
• Vertical design
• NO YELLOW or BLACK AS THE BACKGROUND COLOUR OF ANY SIDE OF THE BIZ CARD

```html
<!DOCTYPE html>
<html lang="en">
<head>
<meta charset="utf-8">
<title>Coastal Learner Bureau – Business Cards</title>
<link rel="stylesheet" href="https://fonts.googleapis.com/css2?family=Open+Sans:wght@400;600;700&family=Tinos:wght@700&display=swap">
<style>
  :root {
    --brand-green: #0b6844;
    --brand-yellow: #e8bb15;
    --card-white: #f3f3f3;
    --page-bg: #dcd8d4;
    --ink-white: #ffffff;
  }
  * { margin: 0; padding: 0; box-sizing: border-box; }
  html, body {
    width: 1200px;
    height: 900px;
    overflow: hidden;
    background: var(--page-bg);
    font-family: "Open Sans", Arial, sans-serif;
  }
  .stage { position: relative; width: 1200px; height: 900px; }

  .card { position: absolute; overflow: hidden; }

  /* Front: green contact side */
  .card--front {
    left: 78px; top: 35px;
    width: 587px; height: 362px;
    background: var(--brand-green);
    color: var(--ink-white);
  }
  .front__accent {
    position: absolute;
    right: 0; top: 0;
    width: 118px; height: 100%;
    background: var(--brand-yellow);
  }
  .front__identity { position: absolute; left: 32px; top: 36px; }
  .front__name {
    font-size: 19px; font-weight: 700; letter-spacing: 0.2px;
    text-transform: uppercase; line-height: 1.2;
  }
  .front__role { font-size: 15.5px; font-weight: 400; line-height: 1.25; }

  .front__watermark {
    position: absolute;
    left: 196px; top: 118px;
    font-size: 84px; font-weight: 700;
    color: var(--ink-white);
    line-height: 1;
    letter-spacing: -1px;
  }

  .contact-list {
    position: absolute; left: 32px; top: 246px;
    list-style: none;
  }
  .contact-list li {
    display: flex; align-items: center;
    font-size: 15.5px; line-height: 21px;
    height: 21px;
  }
  .contact-list li.contact--location { margin-top: 5px; }
  .contact-list svg {
    width: 11px; height: 11px; margin-right: 11px; flex: none;
    fill: var(--ink-white);
  }

  /* Back: white brand side */
  .card--back {
    left: 388px; top: 505px;
    width: 565px; height: 352px;
    background: var(--card-white);
    text-align: center;
  }
  .back__brand {
    position: absolute; left: 0; right: 0; top: 136px;
    font-size: 54px; font-weight: 700;
    color: var(--brand-green);
    line-height: 1;
  }
  .back__tagline {
    position: absolute; left: 0; right: 0; top: 290px;
    font-family: "Tinos", "Times New Roman", serif;
    font-size: 19px; font-weight: 700;
    color: var(--brand-yellow);
    letter-spacing: 0.3px;
  }
</style>
</head>
<body>
<main class="stage">

  <section class="card card--front" aria-label="Business card front">
    <div class="front__accent"></div>
    <div class="front__watermark">Kelvoria</div>

    <div class="front__identity">
      <h1 class="front__name">Tomas Bilbrea</h1>
      <p class="front__role">Managing Director</p>
    </div>

    <ul class="contact-list">
      <li class="contact--phone">
        <svg viewBox="0 0 24 24" aria-hidden="true"><path d="M6.6 10.8a15.1 15.1 0 0 0 6.6 6.6l2.2-2.2a1 1 0 0 1 1-.25 11.4 11.4 0 0 0 3.6.57 1 1 0 0 1 1 1V20a1 1 0 0 1-1 1A17 17 0 0 1 3 4a1 1 0 0 1 1-1h3.5a1 1 0 0 1 1 1c0 1.25.2 2.45.57 3.57a1 1 0 0 1-.25 1z"/></svg>
        +61 491058264
      </li>
      <li class="contact--email">
        <svg viewBox="0 0 24 24" aria-hidden="true"><path d="M2 5h20v14H2z M3.5 6.5 12 13l8.5-6.5" stroke="#0b6844" stroke-width="1.6"/></svg>
        tomas@kelvarin.com.au
      </li>
      <li class="contact--web">
        <svg viewBox="0 0 24 24" aria-hidden="true"><circle cx="12" cy="12" r="10"/><path d="M2 12h20M12 2c3 3 3 17 0 20M12 2c-3 3-3 17 0 20" stroke="#0b6844" stroke-width="1.6" fill="none"/></svg>
        www.kelvoria.com.au
      </li>
      <li class="contact--location">
        <svg viewBox="0 0 24 24" aria-hidden="true"><path d="M12 1a8 8 0 0 0-8 8c0 6 8 14 8 14s8-8 8-14a8 8 0 0 0-8-8zm0 11a3 3 0 1 1 0-6 3 3 0 0 1 0 6z"/></svg>
        Melbourne, Australia
      </li>
    </ul>
  </section>

  <section class="card card--back" aria-label="Business card back">
    <div class="back__brand">Kelvoria</div>
    <p class="back__tagline">HACEMOS MÁS POR TI!</p>
  </section>

</main>
</body>
</html>
```